Health Care Company with Logo Needs Business Cards designed

We are a luxury behavioral health company looking for business cards design we already have a logo and are looking for someone to design a sophisticated luxurious looking business card. Please note that Card design should be captivating just like the logo and also encompass the logo color

Industry/Entity Type

Healthcare

Contact Information for Business Card

Logo,company name, tagline, my name and title, contact details, and physical address

```html
<!DOCTYPE html>
<html lang="en">
<head>
<meta charset="utf-8">
<title>Corin Behavioral Health – Business Cards</title>
<link rel="stylesheet" href="https://fonts.googleapis.com/css2?family=Lato:wght@400;700;900&family=Oswald:wght@500&display=swap">
<style>
  :root {
    --page-bg: #1c1c1c;
    --card-bg: #111111;
    --purple: #7b3f9e;
    --blue: #1aa3e0;
    --white: #f2f2f2;
    --rule: #8a8a8a;
  }
  * { box-sizing: border-box; margin: 0; padding: 0; }
  html, body {
    width: 1200px; height: 900px; overflow: hidden;
    background: var(--page-bg);
    font-family: "Lato", sans-serif;
  }
  .stage {
    position: relative; width: 1200px; height: 900px;
    display: flex; flex-direction: column; align-items: center; justify-content: center; gap: 40px;
  }
  .card {
    position: relative; width: 630px; height: 360px;
    background: var(--card-bg);
    box-shadow: 0 10px 30px rgba(0,0,0,.6);
    overflow: hidden;
  }
  .card__band {
    position: absolute; left: 0; right: 0; bottom: 0; height: 12px;
    background: var(--purple);
  }
  /* Front */
  .brand {
    position: absolute; left: 50%; top: 44%; transform: translate(-50%, -50%);
    display: flex; align-items: center; gap: 18px;
  }
  .brand__mark { width: 54px; height: 54px; background: var(--purple); flex: none; }
  .brand__name {
    font-weight: 900; font-size: 38px; color: var(--purple); letter-spacing: .5px; white-space: nowrap;
  }
  .brand__tagline {
    margin-top: 4px;
    font-weight: 700; font-size: 12.5px; color: var(--blue);
    letter-spacing: 3.4px; text-transform: uppercase; white-space: nowrap;
  }
  /* Back */
  .person {
    position: absolute; left: 70px; top: 120px; text-align: right; width: 250px;
  }
  .person__name {
    font-family: "Oswald", sans-serif; font-weight: 500; font-size: 40px;
    color: var(--purple); text-transform: uppercase; line-height: 1; letter-spacing: -.5px;
  }
  .person__title { font-size: 22px; color: var(--white); margin-top: 2px; }
  .divider {
    position: absolute; left: 345px; top: 120px; width: 1px; height: 90px; background: var(--rule);
  }
  .contacts {
    position: absolute; left: 370px; top: 125px; list-style: none;
    display: flex; flex-direction: column; gap: 6px;
  }
  .contacts__item {
    display: flex; align-items: center; gap: 10px;
    font-size: 20px; color: var(--white); white-space: nowrap;
  }
  .contacts__icon { width: 20px; height: 20px; flex: none; fill: none; stroke: var(--purple); stroke-width: 2; }
  .address {
    position: absolute; left: 70px; bottom: 50px;
    font-size: 20px; color: var(--white); letter-spacing: .3px; white-space: nowrap;
  }
</style>
</head>
<body>
<main class="stage">
  <section class="card card--front">
    <div class="brand">
      <span class="brand__mark"></span>
      <div class="brand__text">
        <div class="brand__name">Corin Behavioral Health</div>
        <div class="brand__tagline">Dedicated to hope, healing and recovery</div>
      </div>
    </div>
    <div class="card__band"></div>
  </section>

  <section class="card card--back">
    <div class="person">
      <div class="person__name">Daniel Reyes</div>
      <div class="person__title">Managing Director</div>
    </div>
    <div class="divider"></div>
    <ul class="contacts">
      <li class="contacts__item">
        <svg class="contacts__icon" viewBox="0 0 24 24" aria-hidden="true"><path d="M5 3h4l2 5-2.5 1.5a11 11 0 0 0 6 6L16 13l5 2v4a2 2 0 0 1-2 2A16 16 0 0 1 3 5a2 2 0 0 1 2-2z"/></svg>
        044-580 217 364
      </li>
      <li class="contacts__item">
        <svg class="contacts__icon" viewBox="0 0 24 24" aria-hidden="true"><rect x="3" y="5" width="18" height="14"/><path d="M3 5l9 8 9-8"/></svg>
        hello@corinhealth.com
      </li>
      <li class="contacts__item">
        <svg class="contacts__icon" viewBox="0 0 24 24" aria-hidden="true"><circle cx="12" cy="12" r="9"/><path d="M3 12h18M12 3c3 3 3 15 0 18M12 3c-3 3-3 15 0 18"/></svg>
        www.corinhealth.com
      </li>
    </ul>
    <div class="address">218, Linden Park Road, Westbrook, 60417</div>
    <div class="card__band"></div>
  </section>
</main>
</body>
</html>
```